business card deign

Logo needs the following on it.
1. attached logo
2. Tagline - "If it keeps a drink cold or the party going...we do it!"
3. Name- Dalton Pikes, Founder and CPO
4. Address - 412 E. Carver Avenue, Ste 2207, Tampa, FL. 33917
5. Phone - 555.318.4726

```html
<!DOCTYPE html>
<html lang="en">
<head>
<meta charset="utf-8">
<title>Kelvaro Business Card</title>
<link rel="stylesheet" href="https://fonts.googleapis.com/css2?family=Montserrat:wght@400;600;700&display=swap">
<style>
  :root {
    --backdrop: #9a9a9a;
    --card-light: #ffffff;
    --card-dark: #2a2a2a;
    --ink: #2b2b2b;
    --ink-soft: #3a3a3a;
    --paper-text: #ffffff;
  }
  html, body {
    margin: 0;
    padding: 0;
    width: 1200px;
    height: 1059px;
    overflow: hidden;
    background: var(--backdrop);
    font-family: "Montserrat", sans-serif;
  }
  .canvas {
    position: relative;
    width: 1200px;
    height: 1059px;
  }
  .card {
    position: absolute;
    border-radius: 18px;
    overflow: hidden;
  }
  .card--front {
    left: 256px; top: 89px; width: 688px; height: 390px;
    background: var(--card-light);
    color: var(--ink);
  }
  .card--back {
    left: 254px; top: 569px; width: 693px; height: 394px;
    background: var(--card-dark);
    color: var(--paper-text);
  }
  .brand { position: absolute; text-align: center; }
  .brand__mark { display: block; margin: 0 auto; border-radius: 50%; }
  .brand__name {
    display: block;
    font-weight: 600;
    letter-spacing: 0.42em;
    text-indent: 0.42em;
  }
  .card--front .brand { left: 40px; top: 52px; width: 196px; }
  .card--front .brand__mark { width: 74px; height: 74px; background: var(--ink); }
  .card--front .brand__name { font-size: 25px; margin-top: 28px; color: var(--ink); }

  .card--back .brand { left: 196px; top: 88px; width: 300px; }
  .card--back .brand__mark { width: 120px; height: 120px; background: var(--paper-text); }
  .card--back .brand__name { font-size: 36px; margin-top: 38px; color: var(--paper-text); }

  .person {
    position: absolute; right: 41px; top: 230px; text-align: right;
  }
  .person__name {
    margin: 0; font-size: 24px; font-weight: 700; letter-spacing: 0.02em; line-height: 1.1;
  }
  .person__title {
    margin: 2px 0 0; font-size: 15.5px; font-weight: 400; color: var(--ink-soft);
  }
  .divider {
    position: absolute; left: 40px; right: 41px; top: 295px;
    border: 0; border-top: 1px solid var(--ink); margin: 0;
  }
  .contact {
    position: absolute; left: 40px; top: 311px;
    margin: 0; padding: 0; list-style: none;
    font-size: 15.5px; color: var(--ink-soft); line-height: 26px;
  }
  .contact__item { display: flex; align-items: center; gap: 7px; }
  .contact__icon { width: 13px; height: 13px; fill: var(--ink); }
  .address {
    position: absolute; right: 41px; top: 312px;
    margin: 0; font-style: normal; text-align: right;
    font-size: 15.5px; color: var(--ink-soft); line-height: 23px;
  }
  .tagline {
    position: absolute; left: 0; right: 0; top: 337px;
    margin: 0; text-align: center; font-size: 15.5px; font-weight: 400;
  }
</style>
</head>
<body>
<main class="canvas">
  <section class="card card--front" aria-label="Card front">
    <div class="brand">
      <span class="brand__mark"></span>
      <span class="brand__name">KELVARO</span>
    </div>
    <div class="person">
      <h1 class="person__name">DALTON PIKES</h1>
      <p class="person__title">Founder and CPO</p>
    </div>
    <hr class="divider">
    <ul class="contact">
      <li class="contact__item">
        <svg class="contact__icon" viewBox="0 0 16 16" aria-hidden="true"><path d="M1 6c0-2 3-4 7-4s7 2 7 4v1h-3V5.5C11 5 9.5 4.8 8 4.8S5 5 4 5.5V7H1zM4 8l2-2h4l2 2 1 6H3z"/></svg>
        555.318.4726
      </li>
      <li class="contact__item">
        <svg class="contact__icon" viewBox="0 0 16 16" aria-hidden="true"><path d="M1 6l7-5 7 5v9H1zM2.5 7v6.5h11V7L8 11z"/></svg>
        dpikes@kelvaro.com
      </li>
    </ul>
    <address class="address">
      412 E. Carver Avenue<br>
      Ste 2207, Tampa, FL. 33917
    </address>
  </section>

  <section class="card card--back" aria-label="Card back">
    <div class="brand">
      <span class="brand__mark"></span>
      <span class="brand__name">KELVARO</span>
    </div>
    <p class="tagline">If it keeps a drink cold or the party going...we do it!</p>
  </section>
</main>
</body>
</html>
```